Web Developer Needs a Business Card Design

I need a personal business card design that represents me as a web developer for potential employers. I would like the background to be a dark color on the front for contrast with my logo and name. The back will have all my information along with a smaller version of the logo. I want something with a modern look and feel, not too conservative. This will be used for potential employers and freelance work.

Industry/Entity Type

Business

Contact Information for Business Card

Front should have my logo and name. The back should have all my personal information which would include: name: Tom Varulek, phone: 570-614-3098, email: tomvarulek@quillbox.net, website url: www.tomvarulek.net, logo, web developer.

Font styles to use
Sans Serif

Requirements
Must have
• Must include my logo. The color palette base color will be the logo color.

```html
<!DOCTYPE html>
<html lang="en">
<head>
<meta charset="utf-8">
<title>Tom Varulek — Business Cards</title>
<link rel="stylesheet" href="https://fonts.googleapis.com/css2?family=Source+Sans+3:wght@400;600;700&display=swap">
<style>
  :root {
    --page-bg: #eceeed;
    --card-mint: #4fe3c1;
    --ink-white: #ffffff;
    --card-font: "Source Sans 3", "Helvetica Neue", Arial, sans-serif;
  }
  * { box-sizing: border-box; margin: 0; padding: 0; }
  html, body {
    width: 1200px;
    height: 900px;
    overflow: hidden;
    background: var(--page-bg);
    font-family: var(--card-font);
    color: var(--ink-white);
  }
  .canvas { position: relative; width: 1200px; height: 900px; }

  .card {
    position: absolute;
    width: 556px;
    height: 344px;
    background: var(--card-mint);
  }
  .card--back {
    left: 240px; top: 62px;
    border-radius: 0 72px 0 72px;
  }
  .card--front {
    left: 460px; top: 518px;
    border-radius: 72px 0 72px 0;
  }

  .brand-mark {
    position: absolute;
    display: flex;
    align-items: center;
    gap: 12px;
    font-weight: 700;
    color: var(--ink-white);
  }
  .brand-mark__ring {
    border: 6px solid var(--ink-white);
    border-radius: 50%;
    flex: none;
  }
  .card--back .brand-mark { right: 46px; top: 80px; font-size: 30px; }
  .card--back .brand-mark__ring { width: 44px; height: 44px; }
  .card--front .brand-mark {
    left: 0; right: 0; top: 110px;
    justify-content: center;
    font-size: 46px;
    gap: 16px;
  }
  .card--front .brand-mark__ring { width: 62px; height: 62px; border-width: 7px; }

  .identity { position: absolute; left: 57px; top: 182px; }
  .identity__name { font-size: 19px; font-weight: 700; line-height: 1.2; }
  .identity__role { font-size: 15px; font-weight: 400; line-height: 1.3; }

  .contact-list {
    position: absolute;
    left: 58px; top: 244px;
    list-style: none;
    font-size: 14.5px;
    line-height: 20.5px;
  }
  .contact-list__item { display: flex; align-items: center; gap: 7px; }
  .contact-list__icon { width: 11px; height: 11px; flex: none; }

  .front-name {
    position: absolute;
    left: 0; right: 0; top: 268px;
    text-align: center;
    font-size: 25px;
    font-weight: 700;
  }
</style>
</head>
<body>
<main class="canvas">

  <section class="card card--back" aria-label="Business card back">
    <div class="brand-mark">
      <span class="brand-mark__ring"></span>
      <span class="brand-mark__name">Varulek</span>
    </div>

    <div class="identity">
      <p class="identity__name">Tom Varulek</p>
      <p class="identity__role">Front-End Developer</p>
    </div>

    <ul class="contact-list">
      <li class="contact-list__item">
        <svg class="contact-list__icon" viewBox="0 0 12 12" aria-hidden="true">
          <path fill="#fff" d="M2.4 0.6l1.9 2.2-1.1 1.3c.7 1.6 2 2.9 3.6 3.6l1.3-1.1 2.2 1.9-.9 2.2C5.2 10.6 1.4 6.8.5 1.5z"/>
        </svg>
        <span>570-614-3098</span>
      </li>
      <li class="contact-list__item">
        <svg class="contact-list__icon" viewBox="0 0 12 12" aria-hidden="true">
          <rect x="1" y="3" width="10" height="7" fill="#fff"/>
          <path d="M1 3l5 4 5-4" fill="none" stroke="#4fe3c1" stroke-width="1"/>
        </svg>
        <span>tomvarulek@quillbox.net</span>
      </li>
      <li class="contact-list__item">
        <svg class="contact-list__icon" viewBox="0 0 12 12" aria-hidden="true">
          <circle cx="6" cy="6" r="5" fill="none" stroke="#fff" stroke-width="1.3"/>
          <ellipse cx="6" cy="6" rx="2.2" ry="5" fill="none" stroke="#fff" stroke-width="1"/>
          <path d="M1 6h10" stroke="#fff" stroke-width="1"/>
        </svg>
        <span>www.tomvarulek.net</span>
      </li>
    </ul>
  </section>

  <section class="card card--front" aria-label="Business card front">
    <div class="brand-mark">
      <span class="brand-mark__ring"></span>
      <span class="brand-mark__name">Varulek</span>
    </div>
    <p class="front-name">Tom Varulek</p>
  </section>

</main>
</body>
</html>
```